Custom Cabinet Shop Needs a website design

Hi,
We need a website for a Custom Cabinet Shop and Cabinet parts manufacturing business.
The business has two sides to it. One side provides custom Kitchens, vanities, entertainment units, offices and what not to homeowners and contractors.
The 2nd side of the business provides built to order cabinet boxes and other parts required to put together a project to other cabinet shops, small contractors looking to install there own cabinets.
Website will need a Gallery to display work.
Color scheme to go well with logo.
current website is www.brambleoakcustomcabinets.com
being changed to www.brambleoak.ca
Logo Included in attached files.
Tagline "Joinery with Spirit"
Mission Statement "Our passion is to deliver inspired cabinetry solutions to suit all your needs, supported by our phenomenal star class customer service"
The website should convey quality and professionalism.
Thank you.
Homeowners/ Contractors
Entertainment

```html
<!DOCTYPE html>
<html lang="en">
<head>
<meta charset="utf-8">
<title>Brambleoak Custom Cabinets</title>
<link rel="stylesheet" href="https://fonts.googleapis.com/css2?family=Roboto:wght@400;500;700&family=Open+Sans:wght@400;600&family=Oswald:wght@500&family=Montserrat:wght@400;500&display=swap">
<style>
:root{
  --orange:#e2461d;
  --orange-dark:#c83a14;
  --black:#000;
  --ink:#222;
  --text:#333;
  --muted:#666;
  --navy:#1c2f5a;
  --footer-bg:#efefef;
  --line:#dcdcdc;
  --white:#fff;
}
*{margin:0;padding:0;box-sizing:border-box}
html,body{width:1200px;height:2182px;overflow:hidden;background:var(--white)}
body{position:relative;font-family:"Open Sans",sans-serif;color:var(--text)}
.abs{position:absolute}

/* header */
.brand{left:98px;top:40px;display:flex;align-items:center;gap:14px}
.brand-dot{width:46px;height:46px;border-radius:50%;background:var(--orange)}
.brand-name{font:700 34px/1 "Roboto",sans-serif;color:var(--ink);letter-spacing:1px}
.head-contact{left:798px;top:36px;display:flex;gap:14px;align-items:flex-start}
.head-contact .divider{width:1px;height:44px;background:var(--line)}
.head-contact p{font:400 15px/1.6 "Roboto",sans-serif;color:var(--ink)}
.head-contact .toll{color:var(--navy);font-weight:500}

.navband{left:0;top:131px;width:1200px;height:59px;background:var(--black)}
.nav{left:521px;top:121px;width:565px;height:69px;background:var(--orange);display:flex;align-items:center;padding-left:20px;gap:0}
.nav::before,.nav::after{content:"";position:absolute;top:0;width:0;height:0;border-top:10px solid transparent}
.nav::before{left:-10px;border-right:10px solid var(--orange-dark)}
.nav::after{right:-10px;border-left:10px solid var(--orange-dark)}
.nav a{font:400 14px "Roboto",sans-serif;color:var(--white);text-decoration:none;margin-right:42px}

/* hero */
.hero{left:0;top:190px;width:1200px;height:533px;background:linear-gradient(90deg,#2a1a18 0%,#3b2220 28%,#b81c22 45%,#d5d3d0 70%,#f2f2f2 100%)}
.hero-floor{left:0;top:560px;width:1200px;height:163px;background:linear-gradient(180deg,rgba(70,35,30,.6),rgba(40,20,18,.9))}
.hero-title{left:98px;top:630px;font:500 48px/1 "Oswald",sans-serif;color:#9a9a9a;text-transform:uppercase}
.hero-arrow{top:459px;width:32px;height:32px;border-radius:50%;background:rgba(0,0,0,.5);display:flex;align-items:center;justify-content:center}

/* services band */
.services{left:0;top:723px;width:1200px;height:177px;background:var(--orange)}
.service{top:45px;display:flex;gap:16px}
.service .ring{width:52px;height:52px;border:2px solid rgba(255,255,255,.85);border-radius:50%;display:flex;align-items:center;justify-content:center;flex:none}
.service h3{font:500 17px "Roboto",sans-serif;color:var(--white);margin-bottom:12px;margin-top:-2px}
.service p{font:400 11.5px/20px "Open Sans",sans-serif;color:#fbe2d8;width:250px}

/* gallery */
.section-title{width:1200px;left:0;text-align:center;font:500 27px "Roboto",sans-serif;color:var(--orange);text-transform:uppercase}
.section-sub{width:1200px;left:0;text-align:center;font:400 14px "Roboto",sans-serif;color:var(--ink)}
.rule{left:98px;width:1004px;height:1px;background:var(--line)}
.rule::after{content:"";position:absolute;left:496px;top:-5px;width:10px;height:10px;background:#e4e4e4;transform:rotate(45deg)}
.card{top:1060px;width:230px;height:330px}
.card .photo{height:249px}
.card .cap{height:81px;background:var(--orange);padding:16px 16px 0;position:relative}
.card h4{font:400 15px "Roboto",sans-serif;color:var(--white)}
.card p{font:400 12px "Roboto",sans-serif;color:var(--white);margin-top:9px}
.card .zoom{position:absolute;right:16px;top:26px;width:28px;height:28px;border-radius:50%;background:#1a1a1a;display:flex;align-items:center;justify-content:center}

/* welcome */
.welcome-photo{left:98px;top:1489px;width:363px;height:280px;background:linear-gradient(160deg,#8d8676,#4d463c 55%,#2a2520)}
.welcome-title{left:491px;top:1482px;font:500 27px "Montserrat",sans-serif;color:var(--ink);text-transform:uppercase}
.welcome-title span{color:var(--orange)}
.welcome-copy{left:495px;top:1530px;width:610px}
.welcome-copy p{font:400 11px/21px "Open Sans",sans-serif;color:var(--ink);margin-bottom:6px}
.mission-icon{left:494px;top:1686px;width:80px;height:80px;border-radius:50%;border:1px solid #e6e6e6;display:flex;align-items:center;justify-content:center}
.mission-title{left:596px;top:1684px;font:400 19px "Montserrat",sans-serif;color:var(--ink);text-transform:uppercase}
.mission-quote{left:602px;top:1722px;width:480px;font:400 13px/22px "Open Sans",sans-serif;color:var(--orange)}

/* footer */
.footer{left:0;top:1838px;width:1200px;height:282px;background:var(--footer-bg)}
.foot-h{font:500 15px "Montserrat",sans-serif;color:var(--ink);text-transform:uppercase}
.news{display:flex;gap:17px}
.news .thumb{width:102px;height:76px;background:linear-gradient(150deg,#b9ad99,#5b5044)}
.news h5{font:400 16px "Open Sans",sans-serif;color:var(--ink)}
.news p{font:400 11px/17px "Open Sans",sans-serif;color:var(--muted);width:180px;margin-top:3px}
.news time{display:block;font:600 11px "Roboto",sans-serif;color:#1e57a8;margin-top:5px}
.foot-list{list-style:none}
.foot-list li{font:400 13px "Open Sans",sans-serif;color:var(--ink)}
.foot-contact p{font:400 13px/21px "Open Sans",sans-serif;color:var(--ink)}
.foot-contact .row{display:flex;align-items:center;gap:14px;font:400 14px "Open Sans",sans-serif;color:var(--ink);letter-spacing:.3px}

.bottom{left:0;top:2120px;width:1200px;height:62px;background:var(--black)}
.copyright{left:0;width:1060px;top:2140px;text-align:center;font:400 14px "Roboto",sans-serif;color:var(--white)}
.social{left:888px;top:2112px;width:212px;height:70px;background:var(--orange);display:flex;align-items:center;justify-content:center;gap:10px}
.social::before,.social::after{content:"";position:absolute;top:0;border-top:8px solid transparent}
.social::before{left:-8px;border-right:8px solid var(--orange-dark)}
.social::after{right:-8px;border-left:8px solid var(--orange-dark)}
.social span{width:26px;height:26px;border-radius:50%;background:var(--white);opacity:.9}
</style>
</head>
<body>

<header>
  <div class="abs brand"><span class="brand-dot"></span><span class="brand-name">BRAMBLEOAK</span></div>
  <div class="abs head-contact">
    <svg width="26" height="36" viewBox="0 0 26 36"><path d="M6 2c3 0 5 7 4 9l-3 2c1 5 4 10 8 13l3-2c2-1 8 3 7 6-1 3-4 5-7 4C9 31 1 20 1 9 1 5 3 2 6 2z" fill="#bdbdbd"/></svg>
    <span class="divider"></span>
    <div><p>info@brambleoakcustomcabinets.com</p><p class="toll">Toll Free : 901-555-0148</p></div>
  </div>
  <div class="abs navband"></div>
  <nav class="abs nav">
    <a href="#">HOME</a><a href="#">GALLERY</a><a href="#">OUR SERVICES</a><a href="#">WARRANTY</a><a href="#">CONTACT US</a>
  </nav>
</header>

<section>
  <div class="abs hero" role="img" aria-label="Modern kitchen with dark wood tall cabinets, built-in ovens and glossy red base cabinets"></div>
  <div class="abs hero-floor"></div>
  <h1 class="abs hero-title">Joinery with Spirit</h1>
  <div class="abs hero-arrow" style="left:34px"><svg width="10" height="14"><path d="M8 1 2 7l6 6" stroke="#ddd" stroke-width="2" fill="none"/></svg></div>
  <div class="abs hero-arrow" style="left:1132px"><svg width="10" height="14"><path d="m2 1 6 6-6 6" stroke="#ddd" stroke-width="2" fill="none"/></svg></div>
</section>

<section class="abs services">
  <div class="abs service" style="left:98px">
    <span class="ring"><svg width="20" height="26" viewBox="0 0 20 26"><path d="M10 2a7 7 0 0 0-4 13v3h8v-3a7 7 0 0 0-4-13z" fill="none" stroke="#fff" stroke-width="2"/><path d="M7 21h6M8 24h4" stroke="#fff" stroke-width="2"/></svg></span>
    <div><h3>DESIGN ASSISTANT</h3><p>Sed ut perspiciatis unde omnis iste natus error sit volu Sed ut perspiciatis unde omnis Sed ut perspiciatis unde omnis iste</p></div>
  </div>
  <div class="abs service" style="left:443px">
    <span class="ring"><svg width="20" height="26" viewBox="0 0 20 26"><rect x="3" y="2" width="14" height="22" fill="none" stroke="#fff" stroke-width="2"/><path d="M7 7h2M11 7h2M7 11h2M11 11h2M7 15h2M11 15h2M8 20h4" stroke="#fff" stroke-width="2"/></svg></span>
    <div><h3>RESIDENTIAL</h3><p>Sed ut perspiciatis unde omnis iste natus error sit volu Sed ut perspiciatis unde omnis Sed ut perspiciatis unde omnis iste</p></div>
  </div>
  <div class="abs service" style="left:805px">
    <span class="ring"><svg width="26" height="22" viewBox="0 0 26 22"><rect x="2" y="2" width="22" height="14" fill="none" stroke="#fff" stroke-width="2"/><path d="M9 20h8M13 16v4" stroke="#fff" stroke-width="2"/></svg></span>
    <div><h3>BUSINESS</h3><p>Sed ut perspiciatis unde omnis iste natus error sit volu Sed ut perspiciatis unde omnis Sed ut perspiciatis unde omnis iste</p></div>
  </div>
</section>

<section>
  <h2 class="abs section-title" style="top:938px">Our Featured Gallery</h2>
  <p class="abs section-sub" style="top:981px">We offer an overflowing portfolio of beautiful furnishing s for you</p>
  <div class="abs rule" style="top:1027px"></div>

  <article class="abs card" style="left:98px"><div class="photo" role="img" aria-label="Dark kitchen with wooden island bar and stools" style="background:linear-gradient(160deg,#5a4a3a,#1e1814)"></div><div class="cap"><h4>Body of Work</h4><p>Brambleoak Custom Cabinets...</p><span class="zoom"><svg width="12" height="12"><circle cx="5" cy="5" r="3.5" stroke="#fff" stroke-width="1.6" fill="none"/><path d="m8 8 3 3" stroke="#fff" stroke-width="1.6"/></svg></span></div></article>
  <article class="abs card" style="left:356px"><div class="photo" role="img" aria-label="White and black kitchen with island and range hood" style="background:linear-gradient(160deg,#9b9a96,#2a2a2a)"></div><div class="cap"><h4>Body of Work</h4><p>Brambleoak Custom Cabinets...</p><span class="zoom"><svg width="12" height="12"><circle cx="5" cy="5" r="3.5" stroke="#fff" stroke-width="1.6" fill="none"/><path d="m8 8 3 3" stroke="#fff" stroke-width="1.6"/></svg></span></div></article>
  <article class="abs card" style="left:613px"><div class="photo" role="img" aria-label="Kitchen island with wine rack and pendant lights" style="background:linear-gradient(160deg,#8a7d6c,#2d241e)"></div><div class="cap"><h4>Body of Work</h4><p>Brambleoak Custom Cabinets...</p><span class="zoom"><svg width="12" height="12"><circle cx="5" cy="5" r="3.5" stroke="#fff" stroke-width="1.6" fill="none"/><path d="m8 8 3 3" stroke="#fff" stroke-width="1.6"/></svg></span></div></article>
  <article class="abs card" style="left:871px"><div class="photo" role="img" aria-label="Bright kitchen with white cabinets and dark island" style="background:linear-gradient(160deg,#c9c6bf,#3a3632)"></div><div class="cap"><h4>Body of Work</h4><p>Brambleoak Custom Cabinets...</p><span class="zoom"><svg width="12" height="12"><circle cx="5" cy="5" r="3.5" stroke="#fff" stroke-width="1.6" fill="none"/><path d="m8 8 3 3" stroke="#fff" stroke-width="1.6"/></svg></span></div></article>

  <div class="abs rule" style="top:1436px"></div>
</section>

<section>
  <div class="abs welcome-photo" role="img" aria-label="Kitchen with granite island, pendant lights and stainless appliances"></div>
  <h2 class="abs welcome-title">Welcome to <span>Brambleoak</span> Custom</h2>
  <div class="abs welcome-copy">
    <p>Lorem ipsum dolor sit amet, consectetur adipiscing elit, sed do eiusmod tempor incididunt ut labore et dolore magna aliqua. Ut enim ad minim veniam, quis nostrud exercitation ullamco laboris nisi ut aliquip ex ea commodo consequat. Duis aute irure dolor in reprehenderit in voluptate velit esse cillum dolore eu fugiat nulla pariatur. Excepteur sint occaecat cupidatat non proident, sunt in culpa qui officia deserunt mollit anim id est laborum</p>
    <p>Lorem ipsum dolor sit amet, consectetur adipiscing elit, sed do eiusmod tempor incididunt ut labore et dolore magna aliqua. Ut enim ad minim veniam, quis nostrud exercitation ullamco laboris nisi</p>
  </div>
  <div class="abs mission-icon"><svg width="36" height="38" viewBox="0 0 36 38"><circle cx="18" cy="11" r="9" fill="#333"/><path d="M2 38c0-11 7-16 16-16s16 5 16 16z" fill="#333"/></svg></div>
  <h3 class="abs mission-title">Our Mission</h3>
  <p class="abs mission-quote">" Our passion is to deliver inspired cabinetry solutions to suit all your needs, supported by our phenomenal star class customer service "</p>
</section>

<footer>
  <div class="abs footer"></div>
  <h4 class="abs foot-h" style="left:98px;top:1868px">Latest News</h4>
  <div class="abs news" style="left:98px;top:1909px"><div class="thumb" role="img" aria-label="Dining room with pendant light"></div><div><h5>Sed ut perspiciatis unde</h5><p>Lorem ipsum dolor sit amet, adip-isicing elit, sed do eiusmod</p><time>25 MARCH. 2015</time></div></div>
  <div class="abs news" style="left:98px;top:2012px"><div class="thumb" role="img" aria-label="Kitchen interior with chandelier"></div><div><h5>Sed ut perspiciatis unde</h5><p>Lorem ipsum dolor sit amet, adip-isicing elit, sed do eiusmod</p><time>25 MARCH. 2015</time></div></div>

  <h4 class="abs foot-h" style="left:450px;top:1872px">Infomation</h4>
  <ul class="abs foot-list" style="left:450px;top:1906px;line-height:22px"><li>Home</li><li>About us</li><li>Portfolio/gallery</li><li>Services</li><li>Contact us</li></ul>

  <h4 class="abs foot-h" style="left:621px;top:1872px">Choose Brambleoak</h4>
  <ul class="abs foot-list" style="left:621px;top:1906px;line-height:28.5px"><li>Custom Homes</li><li>Residential</li><li>Furniture</li><li>Business</li></ul>

  <h4 class="abs foot-h" style="left:831px;top:1872px">Contact Us</h4>
  <div class="abs foot-contact" style="left:831px;top:1899px">
    <p>4120 Cedar Mill Road<br>Rocky View, Alberta T1X 0A0</p>
    <div class="row" style="margin-top:14px"><svg width="18" height="18" viewBox="0 0 26 36"><path d="M6 2c3 0 5 7 4 9l-3 2c1 5 4 10 8 13l3-2c2-1 8 3 7 6-1 3-4 5-7 4C9 31 1 20 1 9 1 5 3 2 6 2z" fill="none" stroke="#1e57a8" stroke-width="2"/></svg>403-555-0172</div>
    <div class="row" style="margin-top:6px"><svg width="18" height="14" viewBox="0 0 18 14"><rect x="1" y="1" width="16" height="12" fill="none" stroke="#1e57a8" stroke-width="1.5"/><path d="m1 1 8 7 8-7" fill="none" stroke="#1e57a8" stroke-width="1.5"/></svg>sales@brambleoakcustomcabinets.com</div>
  </div>

  <div class="abs bottom"></div>
  <p class="abs copyright">Copyright©2015 Brambleoak Custom Cabinets</p>
  <div class="abs social" aria-label="Social links"><span></span><span></span><span></span><span></span><span></span></div>
</footer>

</body>
</html>
```